Emergency and Referral Vet Hospital promotional sticker design

We're looking at getting some stickers designed that we could give to clients to put on their cars for promotion and advertising. If they could also be suitable for a goodie bag for conference too that would be great. I like the look of water-colour backgrounds, we'll need to include our logo and probably our address (Unit 3/215 Korrinup Road Tallowmere). We also have a hospital motto "... because they're family" if that could somehow be integrated, we only care for small animals (dogs, cats etc) but the design is very open to suggestion. Would love to see what you can create.

Industry/Entity Type

Veterinary

Colors
0054AA
0677BA
7BADD7
CADEEF
E8F1F8
0094D4
00A9DD
6FCCEA
C7EBF8
E9F6FB

Requirements
Nice to have
• Think beach vibes, blues maybe paw print shapes etc

```html
<!DOCTYPE html>
<html lang="en">
<head>
<meta charset="utf-8">
<title>Tidewell Vet Hospital – Paw Sticker</title>
<link rel="stylesheet" href="https://fonts.googleapis.com/css2?family=Comfortaa:wght@600&family=Fira+Sans:ital,wght@1,600&family=Questrial&display=swap">
<style>
  :root {
    --canvas-grey: #cccccc;
    --sticker-edge: #ffffff;
    --pad-white: #ffffff;
    --ink-plum: #2e1a2e;
    --mark-teal: #1e6f8c;
    --address-cream: #f3ead8;
    --wash-light: #a9d3d8;
    --wash-mid: #5fa3bd;
    --wash-deep: #2b6a8e;
    --wash-navy: #17496b;
  }
  html, body {
    margin: 0;
    padding: 0;
    width: 1200px;
    height: 1200px;
    overflow: hidden;
    background: var(--canvas-grey);
  }
  .sticker-canvas {
    display: block;
    width: 1200px;
    height: 1200px;
  }
  .sticker-edge ellipse {
    fill: var(--sticker-edge);
    stroke: var(--sticker-edge);
    stroke-width: 44;
  }
  .pad { fill: var(--pad-white); }
  .brand-mark { fill: var(--mark-teal); }
  .brand-name {
    font-family: "Questrial", sans-serif;
    font-size: 36px;
    fill: var(--ink-plum);
    letter-spacing: 1px;
  }
  .motto {
    font-family: "Fira Sans", sans-serif;
    font-style: italic;
    font-weight: 600;
    font-size: 20px;
    fill: var(--ink-plum);
  }
  .address {
    font-family: "Comfortaa", sans-serif;
    font-weight: 600;
    font-size: 19px;
    fill: var(--address-cream);
  }
</style>
</head>
<body>
<svg class="sticker-canvas" viewBox="0 0 1200 1200" xmlns="http://www.w3.org/2000/svg">
  <defs>
    <clipPath id="paw-shape">
      <ellipse cx="655" cy="600" rx="115" ry="125"/>
      <ellipse cx="810" cy="590" rx="120" ry="125"/>
      <ellipse cx="545" cy="760" rx="90" ry="110"/>
      <ellipse cx="930" cy="745" rx="80" ry="110"/>
      <ellipse cx="735" cy="800" rx="240" ry="170"/>
      <ellipse cx="640" cy="920" rx="130" ry="75"/>
      <ellipse cx="840" cy="920" rx="130" ry="75"/>
    </clipPath>
    <linearGradient id="wash-base" x1="0" y1="0" x2="0" y2="1">
      <stop offset="0" stop-color="var(--wash-light)"/>
      <stop offset="0.5" stop-color="var(--wash-mid)"/>
      <stop offset="1" stop-color="var(--wash-navy)"/>
    </linearGradient>
    <radialGradient id="wash-glow" cx="0.55" cy="0.45" r="0.45">
      <stop offset="0" stop-color="#c7ebf8" stop-opacity="0.8"/>
      <stop offset="1" stop-color="#c7ebf8" stop-opacity="0"/>
    </radialGradient>
    <path id="address-curve" d="M572 972 Q738 935 912 975"/>
  </defs>

  <g transform="scale(0.8185)">
    <g class="sticker-edge">
      <ellipse cx="655" cy="600" rx="115" ry="125"/>
      <ellipse cx="810" cy="590" rx="120" ry="125"/>
      <ellipse cx="545" cy="760" rx="90" ry="110"/>
      <ellipse cx="930" cy="745" rx="80" ry="110"/>
      <ellipse cx="735" cy="800" rx="240" ry="170"/>
      <ellipse cx="640" cy="920" rx="130" ry="75"/>
      <ellipse cx="840" cy="920" rx="130" ry="75"/>
    </g>

    <g clip-path="url(#paw-shape)" role="img" aria-label="Blue and aqua watercolour wash filling the paw print">
      <rect x="400" y="440" width="640" height="580" fill="url(#wash-base)"/>
      <rect x="400" y="440" width="640" height="580" fill="url(#wash-glow)"/>
    </g>

    <g class="toe-pads">
      <ellipse class="pad" cx="658" cy="613" rx="62" ry="85"/>
      <ellipse class="pad" cx="806" cy="603" rx="62" ry="85"/>
      <ellipse class="pad" cx="556" cy="750" rx="50" ry="82"/>
      <ellipse class="pad" cx="908" cy="745" rx="50" ry="82"/>
    </g>

    <path class="pad main-pad" d="M735 718 C800 718 840 790 870 830 C900 870 900 930 830 928 C790 926 770 917 735 917 C700 917 680 926 640 928 C570 930 570 870 600 830 C630 790 670 718 735 718 Z"/>

    <circle class="brand-mark" cx="738" cy="786" r="28"/>
    <text class="brand-name" x="738" y="860" text-anchor="middle">Tidewell</text>
    <text class="motto" x="733" y="897" text-anchor="middle">“... because they’re family”</text>

    <text class="address">
      <textPath href="#address-curve" textLength="340" lengthAdjust="spacingAndGlyphs">Unit 3/215 Korrinup Road Tallowmere</textPath>
    </text>
  </g>
</svg>
</body>
</html>
```